Meridale Nutrition needs Stationary and a business card

We would like to use our current logo. The text can be moved around as needed. The stationary needs to be a 'first page' where the logo is more prominent to be impressive on higher quality paper and a second page where the logo is more subtle where there will be much more information on the page. There are 2 clinic locations which will need include name, address, phone number, fax number, web address. The business card should be single sided and contain this information also.
The design must be contemporary and sophisticated as this is a science based diet run out of a medical clinic.

Target Market(s)

People wanting to lose weight, athletes looking to optimise performance, people with arthritis or fighting cancer

Industry/Entity Type

Business

Contact Information for Business Card

must use the logo. I have attached an example card with the practice details on it. there must be space for the doctors name. Also the website www.meridalenutrition.com.au

Requirements
Must have
• the logo, the business adresses and phone numbers, the website, the doctors name and qualifications
Nice to have
• some creativity
Should not have
• Do not simply reproduce the existing card please

```html
<!DOCTYPE html>
<html lang="en">
<head>
<meta charset="utf-8">
<title>Meridale Nutrition Stationery</title>
<link href="https://fonts.googleapis.com/css2?family=EB+Garamond:wght@400;600&family=Jost:wght@400;600&display=swap" rel="stylesheet">
<style>
  :root {
    --backdrop: #9d9ea2;
    --paper: #ffffff;
    --tint: #e2f1fc;
    --brand-blue: #2e6fae;
    --sky: #3fb6ec;
    --ink: #3a3f46;
    --faint: rgba(46, 111, 174, 0.07);
  }
  * { margin: 0; padding: 0; box-sizing: border-box; }
  html, body { width: 1200px; height: 1200px; overflow: hidden; }
  body { background: var(--backdrop); position: relative; font-family: "EB Garamond", serif; color: var(--ink); }

  .sheet {
    position: absolute; top: 60px; width: 480px; height: 680px;
    background: linear-gradient(to bottom, var(--paper) 45%, var(--tint) 100%);
    overflow: hidden;
  }
  .sheet--first { left: 60px; }
  .sheet--second { left: 660px; }

  .masthead { position: absolute; top: 28px; left: 0; right: 0; height: 110px; }
  .masthead__rule { position: absolute; top: 92px; height: 1.5px; background: var(--sky); }
  .masthead__rule--left { left: 0; width: 150px; }
  .masthead__rule--right { right: 0; width: 150px; }
  .masthead__mark { position: absolute; left: 50%; top: 0; width: 66px; height: 66px; margin-left: -33px; border-radius: 50%; background: var(--sky); border: 3px solid var(--brand-blue); }
  .brand-name { font-family: "Jost", sans-serif; font-weight: 600; color: var(--brand-blue); text-transform: uppercase; letter-spacing: 0.5px; white-space: nowrap; }
  .masthead .brand-name { position: absolute; top: 78px; left: 0; right: 0; text-align: center; font-size: 17px; }

  .watermark__ring { position: absolute; right: -60px; top: 150px; width: 340px; height: 340px; border-radius: 50%; background: var(--faint); }
  .watermark__name { position: absolute; right: -40px; top: 470px; font-size: 62px; color: var(--faint); }

  .footer { position: absolute; left: 24px; right: 24px; bottom: 34px; display: flex; justify-content: space-between; text-align: center; }
  .clinic__place { font-size: 15px; display: block; color: #222; }
  .clinic__line { font-size: 11.5px; display: block; line-height: 1.35; }
  .clinic__specialty { font-weight: 600; color: #222; }

  .card {
    position: absolute; left: 380px; top: 820px; width: 440px; height: 250px;
    background: linear-gradient(100deg, #d3ecfb 0%, #f4fafe 45%, var(--paper) 70%);
    overflow: hidden;
  }
  .card__motif { position: absolute; left: -70px; top: 20px; width: 210px; height: 210px; border-radius: 50%; background: rgba(63, 182, 236, 0.18); }
  .card__person { position: absolute; left: 24px; top: 40px; }
  .card__name { font-family: "Jost", sans-serif; font-size: 22px; color: var(--brand-blue); }
  .card__quals { font-size: 8.5px; display: block; }
  .card__role { font-size: 10px; display: block; }
  .card__brand { position: absolute; right: 22px; top: 18px; text-align: center; }
  .card__mark { width: 46px; height: 46px; margin: 0 auto 4px; border-radius: 50%; background: var(--sky); border: 2px solid var(--brand-blue); }
  .card__brand .brand-name { font-size: 11px; }
  .card__clinics { position: absolute; right: 22px; top: 96px; text-align: right; }
  .card__clinics .clinic { margin-bottom: 8px; }
  .card__clinics .clinic__place { font-size: 12px; }
  .card__clinics .clinic__line { font-size: 9px; }
</style>
</head>
<body>

<section class="sheet sheet--first" aria-label="Letterhead first page">
  <header class="masthead">
    <div class="masthead__rule masthead__rule--left"></div>
    <div class="masthead__rule masthead__rule--right"></div>
    <div class="masthead__mark"></div>
    <div class="brand-name">Meridale Nutrition</div>
  </header>
  <footer class="footer">
    <div class="clinic">
      <span class="clinic__place">Westbrook</span>
      <span class="clinic__line">88 Calder Street, Westbrook NSW 2090</span>
      <span class="clinic__line">02 9400 1820 <span class="clinic__specialty">Knee Surgery</span> www.westbrookknee.com.au</span>
    </div>
    <div class="clinic">
      <span class="clinic__place">Harlow</span>
      <span class="clinic__line">12-14 Linden Road, Harlow NSW 2145</span>
      <span class="clinic__line">02 9400 3715 <span class="clinic__specialty">Shoulder &amp; Elbow</span> www.marrowortho.com.au</span>
    </div>
  </footer>
</section>

<section class="sheet sheet--second" aria-label="Letterhead second page">
  <div class="watermark__ring"></div>
  <div class="watermark__name brand-name">Nutrition</div>
  <footer class="footer">
    <div class="clinic">
      <span class="clinic__place">Westbrook</span>
      <span class="clinic__line">88 Calder Street, Westbrook NSW 2090</span>
      <span class="clinic__line">02 9400 1820 <span class="clinic__specialty">Knee Surgery</span> www.westbrookknee.com.au</span>
    </div>
    <div class="clinic">
      <span class="clinic__place">Harlow</span>
      <span class="clinic__line">12-14 Linden Road, Harlow NSW 2145</span>
      <span class="clinic__line">02 9400 3715 <span class="clinic__specialty">Shoulder &amp; Elbow</span> www.marrowortho.com.au</span>
    </div>
  </footer>
</section>

<section class="card" aria-label="Business card">
  <div class="card__motif"></div>
  <div class="card__person">
    <div class="card__name">Dr Elias Marrow</div>
    <span class="card__quals">MBBS MBiomedE FRACS (Ortho)</span>
    <span class="card__role">Orthopaedic Surgeon</span>
  </div>
  <div class="card__brand">
    <div class="card__mark"></div>
    <div class="brand-name">Meridale Nutrition</div>
  </div>
  <div class="card__clinics">
    <div class="clinic">
      <span class="clinic__place">Harlow</span>
      <span class="clinic__line">12-14 Linden Road, Harlow NSW 2145</span>
      <span class="clinic__line">02 9400 3715 <span class="clinic__specialty">Shoulder &amp; Elbow</span> www.marrowortho.com.au</span>
    </div>
    <div class="clinic">
      <span class="clinic__place">Westbrook</span>
      <span class="clinic__line">88 Calder Street, Westbrook NSW 2090</span>
      <span class="clinic__line">02 9400 1820 <span class="clinic__specialty">Knee Surgery</span> www.westbrookknee.com.au</span>
    </div>
  </div>
</section>

</body>
</html>
```